Business IT Services Billboard to attract local small businesses

We are Brivoqua, a premier Managed Service Provider (MSP) specializing in comprehensive IT services and VOIP phone solutions exclusively for businesses. Our goal is to create a dynamic and visually engaging billboard advertisement that not only highlights our cutting-edge IT solutions but also emphasizes our state-of-the-art VOIP phone services. This billboard should communicate our commitment to providing innovative, reliable, and holistic technology solutions.
See the attached supporting documentation.
Target Market(s)
small business
Industry/Entity Type
Information Technology
Colors
Designer to choose colors to be used in the design.
Look and feel
Each slider illustrates characteristics of the customer's brand and the style your logo design should communicate.

```html
<!DOCTYPE html>
<html lang="en">
<head>
<meta charset="utf-8">
<title>Brivoqua Billboard</title>
<link rel="stylesheet" href="https://fonts.googleapis.com/css2?family=Poppins:wght@600;700&family=Oswald:wght@500&display=swap">
<style>
  :root {
    --page-bg: #c4c4c4;
    --navy: #142840;
    --navy-deep: #0f1f33;
    --orange: #df5a0e;
    --panel-gray: #e4e5e8;
    --brand-blue: #1d6bbd;
    --ink: #222426;
    --white: #ffffff;
    --photo-warm: #7a4f36;
    --photo-dark: #1d2430;
  }
  html, body {
    margin: 0;
    padding: 0;
    width: 1038px;
    height: 1200px;
    overflow: hidden;
    background: var(--page-bg);
  }
  .billboard {
    position: absolute;
    left: 39px;
    top: 460px;
    width: 960px;
    height: 280px;
    box-shadow: 0 3px 6px rgba(0,0,0,0.35);
  }
  .billboard svg { display: block; }
  .headline-top { font-family: "Poppins", sans-serif; font-weight: 600; fill: var(--orange); }
  .headline-main { font-family: "Poppins", sans-serif; font-weight: 700; fill: var(--white); }
  .tagline { font-family: "Oswald", sans-serif; font-weight: 500; fill: var(--white); }
  .brand-name { font-family: "Poppins", sans-serif; font-weight: 700; fill: var(--brand-blue); }
  .cta-lead { font-family: "Poppins", sans-serif; font-weight: 600; fill: var(--ink); }
  .cta-url { font-family: "Poppins", sans-serif; font-weight: 700; fill: var(--ink); }
  .cta-url .url-name { fill: var(--brand-blue); }
</style>
</head>
<body>
  <div class="billboard">
    <svg width="960" height="280" viewBox="0 0 960 280" xmlns="http://www.w3.org/2000/svg">
      <defs>
        <linearGradient id="photoTone" x1="0" y1="0" x2="1" y2="1">
          <stop offset="0" stop-color="#c9c3bb"/>
          <stop offset="0.35" stop-color="var(--photo-warm)"/>
          <stop offset="1" stop-color="var(--photo-dark)"/>
        </linearGradient>
        <linearGradient id="navyTone" x1="0" y1="0" x2="1" y2="1">
          <stop offset="0" stop-color="var(--navy)"/>
          <stop offset="1" stop-color="var(--navy-deep)"/>
        </linearGradient>
      </defs>

      <rect class="team-photo" x="660" y="0" width="300" height="280" fill="url(#photoTone)" role="img" aria-label="Photo of support staff with headsets working at computers in a bright office"/>

      <polygon class="headline-panel" points="0,0 688,0 731,126 0,126" fill="url(#navyTone)"/>
      <polygon class="tagline-band" points="0,126 748,126 722,178 0,178" fill="var(--orange)"/>
      <polygon class="contact-panel" points="0,178 722,178 688,280 0,280" fill="var(--panel-gray)"/>

      <text class="headline-top" x="25" y="57" font-size="29" textLength="652" lengthAdjust="spacingAndGlyphs">SEAMLESS TECHNOLOGY SOLUTIONS</text>
      <text class="headline-main" x="25" y="104" font-size="46" textLength="670" lengthAdjust="spacingAndGlyphs">FOR MODERN BUSINESSES</text>

      <text class="tagline" x="25" y="164" font-size="28" textLength="697" lengthAdjust="spacingAndGlyphs">INNOVATIVE IT AND VOIP SOLUTIONS TAILORED FOR YOUR BUSINESS SUCCESS</text>

      <text class="brand-name" x="25" y="236" font-size="20" textLength="90" lengthAdjust="spacingAndGlyphs">Brivoqua</text>

      <text class="cta-lead" x="136" y="216" font-size="19" textLength="464" lengthAdjust="spacingAndGlyphs">TRANSFORM YOUR TECH TODAY AT</text>
      <text class="cta-url" x="136" y="255" font-size="36" textLength="526" lengthAdjust="spacingAndGlyphs">www.<tspan class="url-name">brivoqua</tspan>.com</text>
    </svg>
  </div>
</body>
</html>
```